Corporate Business Card

Very professional, Modern, Not to busy, include phone address email, website
(253) 617-4930, 18761 52nd Avenue S, Kent, WA 98047, martin@plumlinegroup.com, varkoworks.com

Target Market(s)

Manufacturing

Industry/Entity Type

Aero, machining, manufacturing, Off road racing

Contact Information for Business Card

Phone, address email, website

```html
<!DOCTYPE html>
<html lang="en">
<head>
<meta charset="utf-8">
<title>Varko Works – Business Card</title>
<link href="https://fonts.googleapis.com/css2?family=Orbitron:wght@700&family=Roboto:wght@400&display=swap" rel="stylesheet">
<style>
  :root {
    --backdrop: #2b2b2b;
    --navy: #2c3a6c;
    --navy-deep: #26335f;
    --navy-pattern: #34447a;
    --red: #b3201f;
    --grey: #8a8a8a;
    --white: #f2f2f2;
  }
  * { margin: 0; padding: 0; box-sizing: border-box; }
  html, body {
    width: 1200px; height: 1138px; overflow: hidden;
    background: var(--backdrop);
  }
  .card {
    position: absolute;
    border-radius: 16px;
    overflow: hidden;
    background: linear-gradient(180deg, var(--navy) 0%, var(--navy-deep) 100%);
  }
  .card-front { left: 274px; top: 186px; width: 623px; height: 376px; }
  .card-back  { left: 276px; top: 608px; width: 618px; height: 374px; }

  .front-pattern {
    position: absolute; inset: 0;
    background: linear-gradient(135deg, var(--navy-deep) 0%, var(--navy-pattern) 55%, var(--navy) 100%);
  }
  .wordmark {
    position: absolute;
    font-family: "Orbitron", sans-serif;
    font-weight: 700;
    font-size: 20px;
    line-height: 24px;
    color: var(--white);
    letter-spacing: 0;
    white-space: nowrap;
    display: flex; align-items: center; gap: 8px;
  }
  .wordmark-mark { width: 12px; height: 12px; background: var(--red); flex: none; }
  .card-front .wordmark { left: 52px; top: 296px; }
  .card-back .wordmark  { left: 44px; top: 158px; }

  .contact { position: absolute; left: 314px; top: 116px; }
  .contact-name {
    font-family: "Orbitron", sans-serif; font-weight: 700;
    font-size: 22px; color: var(--white); letter-spacing: 0.5px;
    margin-bottom: 10px;
  }
  .contact-list { list-style: none; }
  .contact-item {
    font-family: "Roboto", sans-serif; font-size: 16.5px;
    color: var(--white); height: 25px;
    display: flex; align-items: center; gap: 15px;
  }
  .contact-icon { width: 16px; height: 16px; flex: none; }

  .address-band {
    position: absolute; right: 0; bottom: 0;
    width: 391px; height: 45px;
    background: var(--red);
    clip-path: polygon(18px 0, 100% 0, 100% 100%, 0 100%);
    font-family: "Roboto", sans-serif; font-size: 16.5px; color: var(--white);
    display: flex; align-items: center; justify-content: center;
    padding-left: 18px;
  }
  .grey-strip {
    position: absolute; left: 0; bottom: 0;
    width: 230px; height: 14px; background: var(--grey);
  }
</style>
</head>
<body>
  <section class="card card-front">
    <div class="front-pattern" role="img" aria-label="Faint embossed repeating brand pattern across the card face"></div>
    <div class="wordmark"><span class="wordmark-mark"></span>VARKO WORKS</div>
  </section>

  <section class="card card-back">
    <div class="wordmark"><span class="wordmark-mark"></span>VARKO WORKS</div>

    <div class="contact">
      <p class="contact-name">MARTIN HALE</p>
      <ul class="contact-list">
        <li class="contact-item">
          <svg class="contact-icon" viewBox="0 0 16 16"><path fill="#b3201f" d="M1 5c0-2 2-3 7-3s7 1 7 3v1h-4V5H5v1H1zM3 7h10l1 6H2z"/></svg>
          (253) 617-4930
        </li>
        <li class="contact-item">
          <svg class="contact-icon" viewBox="0 0 16 16"><rect x="1" y="3" width="14" height="10" fill="#b3201f"/><path d="M1 3l7 6 7-6" fill="none" stroke="#2c3a6c" stroke-width="1.3"/></svg>
          martin@plumlinegroup.com
        </li>
        <li class="contact-item">
          <svg class="contact-icon" viewBox="0 0 16 16" fill="none" stroke="#b3201f" stroke-width="1.3"><circle cx="8" cy="8" r="6.5"/><ellipse cx="8" cy="8" rx="3" ry="6.5"/><path d="M1.5 8h13M2.5 5h11M2.5 11h11"/></svg>
          www.varkoworks.com
        </li>
      </ul>
    </div>

    <div class="grey-strip"></div>
    <div class="address-band">18761 52nd Avenue S, Kent, WA 98047</div>
  </section>
</body>
</html>
```